Online tuition webpage design needed

Hi,
We are starting up an online tuition website for non- English speakers wishing to take an TOVAR test.

The webpage must include a place for people to enroll online in the course.
The home page must have:
• room for a logo (coming shortly, blue in colour)
• different packages of online tuition and paywick
• tool bar showing different pages
• perhaps a video, small pictures

This is my site currently:-

www.lexavotutoring.com

as you can see, I am not very sure how to create a website … The large logo is what I would like to use, but I project has not been finalized yet. Please note, I don’t like the logo being that large!

Sites that are similar to what I am doing and like the design of are:

http://www.brindacourse.com.au/fees

https://www.quorvel9x.net/index.php

http://www.lessonmasterpercival.co.uk/index.html

http://www.tamrunexamhub.com/

One thing I need is a place for student s to enroll, and if possible, I would like to use learnix to create exercises for students.
Currently, my site is using sitecraft. My preference is to use learnix for online activities. I am not sure if I can use both.
Thanks in advance

Target Market(s)

people wising to take an TOVAR test (English proficiency test)

Industry/Entity Type

Online

Colors
3276b5
0292cd

Requirements
Must have
• a place for enrollment and admin login for students
learnix
video
voxly, friendbook, chirpnet logos
Nice to have
• a booking calender
Should not have
• too much clutter. must be clean and professional looking

```html
<!DOCTYPE html>
<html lang="en">
<head>
<meta charset="utf-8">
<title>TOVAR Online Tuition</title>
<link href="https://fonts.googleapis.com/css2?family=Open+Sans:wght@300;400;600;700&family=Roboto+Condensed:wght@400&family=Lora:ital@1&display=swap" rel="stylesheet">
<style>
:root{
  --brand:#1740a8;
  --sky:#0292cd;
  --sky-dark:#0378b0;
  --steel:#3276b5;
  --gold:#e0a122;
  --orange:#f39c12;
  --ink:#444;
  --line:#e2e2e2;
  --footer:#3b3b3b;
  --green:#3aa64a;
  --red:#e4553c;
}
*{box-sizing:border-box;margin:0;padding:0}
html,body{width:823px;height:1200px;overflow:hidden;background:#fff}
body{position:relative;font-family:"Open Sans",Arial,sans-serif;color:var(--ink)}
.abs{position:absolute}

/* header */
.logo{left:62px;top:30px;display:flex;align-items:center;gap:8px}
.logo-dot{width:34px;height:34px;border-radius:50%;background:var(--brand)}
.logo-name{font-size:32px;font-weight:600;color:var(--brand);line-height:1;letter-spacing:1px}
.logo-tag{left:104px;top:72px;font-size:12px;color:var(--brand)}
.call-btn{left:590px;top:23px;height:21px;width:91px;background:#333;color:#fff;font-size:10.5px;border-radius:2px;display:flex;align-items:center;padding-left:22px}
.call-dot{left:577px;top:20px;width:26px;height:26px;border-radius:50%;background:#1ca8e6;border:2px solid #fff;box-shadow:0 0 0 1px #bbb}
.login-btn{left:697px;top:20px;width:66px;height:24px;background:var(--gold);color:#fff;font-size:11.5px;display:flex;align-items:center;justify-content:center;border-radius:2px}
.search{left:584px;top:70px;width:179px;height:24px;border:1px solid #d8d8d8;font-size:10px;color:#888;padding:5px 9px}
.search svg{position:absolute;right:7px;top:6px}

/* nav */
.nav{left:0;top:111px;width:823px;height:33px;background:var(--sky);border-top:2px solid var(--sky-dark);display:flex;padding-left:59px}
.nav a{font-family:"Roboto Condensed",Arial,sans-serif;color:#fff;text-decoration:none;font-size:11.5px;display:flex;align-items:center;justify-content:center;border-right:1px solid #2aa5d9}
.nav a.active{background:var(--sky-dark)}

/* hero */
.hero{left:0;top:144px;width:823px;height:274px;background:linear-gradient(180deg,#c9d3dc 0%,#e9edf0 45%,#cfcfcf 70%,#a9a9a9 100%)}
.hero-title{left:59px;top:196px;font-size:24px;font-weight:600;color:var(--brand);line-height:1.2}
.hero-sub{left:58px;top:235px;font-size:17px;font-weight:300;color:#333;line-height:1.2}
.hero-text{left:59px;top:267px;font-size:9.5px;line-height:20px;color:#333;white-space:nowrap}
.enroll{left:59px;top:318px;width:111px;height:30px;background:var(--gold);color:#fff;font-size:12.5px;display:flex;align-items:center;justify-content:center;font-family:"Roboto Condensed",sans-serif}
.dots{left:59px;top:373px;display:flex;gap:3px}
.dots i{width:6px;height:6px;border-radius:50%;background:#333}
.dots i:first-child{background:#fff;border:1px solid #333}
.video{left:432px;top:197px;width:284px;height:172px;background:#111;box-shadow:0 2px 6px rgba(0,0,0,.4)}
.video-frame{left:0;top:0;width:284px;height:148px;background:linear-gradient(120deg,#6d7378,#4a5056 50%,#8a7a70)}
.controls{left:0;top:148px;width:284px;height:24px;background:#1b1b1b}

/* welcome */
.h-section{font-family:Arial,sans-serif;font-size:14px;color:var(--sky);line-height:1.2}
.welcome-h{left:59px;top:455px}
.welcome-p{left:59px;top:489px;font-family:Arial,sans-serif;font-size:8.5px;line-height:16.5px;color:#555;white-space:nowrap}
.features{left:59px;top:566px;list-style:none;font-family:Arial,sans-serif;font-size:8.8px;color:#555}
.features li{display:flex;align-items:center;gap:8px;height:23px}
.features li::before{content:"";width:8px;height:8px;border-radius:50%;background:#888;box-shadow:inset 0 0 0 2px #bbb}

/* calendar */
.cal{left:565px;top:458px;width:198px;border:1px solid #ddd}
.cal-head{height:30px;background:linear-gradient(#4a4a4a,#2c2c2c);color:#fff;font-size:10.5px;font-weight:600;display:flex;align-items:center;justify-content:space-between;padding:0 11px}
.cal-grid{display:grid;grid-template-columns:repeat(7,1fr)}
.cal-grid span{height:28px;display:flex;align-items:center;justify-content:center;font-size:8px;font-weight:600;color:#333;border-right:1px solid #e8e8e8;border-bottom:1px solid #e8e8e8;position:relative}
.cal-grid .dn{height:20px;font-size:6.5px;font-weight:400;color:#777}
.cal-grid .off{color:#999;font-weight:400}
.cal-grid .ev::after{content:"";position:absolute;bottom:5px;width:2px;height:2px;background:#333;border-radius:50%}
.cal-grid .today{background:#1565e0;color:#fff;box-shadow:inset 0 0 0 2px #5a9af5}
.cal-grid .today::after{background:#fff}

/* packages */
.pk-h{left:0;width:823px;top:706px;text-align:center}
.pk-frame{left:58px;top:755px;width:707px;height:312px;background:#efefef;border-radius:4px}
.card{background:#fff;border:1px solid #ddd;text-align:center}
.card.pop{border:2px solid var(--orange);box-shadow:0 0 4px rgba(0,0,0,.15)}
.card h3{font-size:23px;font-weight:600;color:#333;line-height:1.2}
.card.pop h3{color:var(--orange)}
.price{font-family:"Lora",Georgia,serif;font-style:italic;font-size:16px;color:#999;margin-top:4px}
.list{list-style:none;margin:14px auto 0;width:176px;border-top:1px solid var(--line)}
.list li{height:25px;border-bottom:1px solid var(--line);display:flex;align-items:center;gap:9px;padding-left:25px;font-size:9.5px;color:#555}
.pay{margin:28px auto 0;width:141px;height:28px;border-radius:14px;background:linear-gradient(#ffd76a,#f4a817);border:1px solid #d99315;color:#1c3f8c;font-size:11px;font-weight:700;display:flex;align-items:center;justify-content:center}
.ribbon{left:463px;top:752px;width:56px;height:56px;overflow:hidden}
.ribbon b{position:absolute;left:-4px;top:14px;width:80px;height:12px;background:var(--orange);transform:rotate(45deg);color:#fff;font-size:6px;font-weight:700;text-align:center;line-height:12px;letter-spacing:.3px}

/* footer */
.footer{left:0;top:1118px;width:823px;height:82px;background:var(--footer);color:#eee;font-family:Arial,sans-serif;font-size:9.5px}
.footer-links{left:60px;top:22px}
.copyright{left:60px;top:46px}
.social{left:624px;top:30px;display:flex;gap:9px}
.social span{width:25px;height:25px;display:flex;align-items:center;justify-content:center;color:#fff;font-size:4.6px;font-family:"Open Sans",sans-serif;font-weight:600}
</style>
</head>
<body>

<header>
  <div class="abs logo"><span class="logo-dot"></span><span class="logo-name">TOVAR</span></div>
  <div class="abs logo-tag">Online Tuition</div>
  <div class="abs call-btn">CALL NOW</div>
  <div class="abs call-dot" aria-label="voxly"></div>
  <div class="abs login-btn">LOGIN</div>
  <div class="abs search">Search..
    <svg width="10" height="10" viewBox="0 0 10 10"><circle cx="4" cy="4" r="3" fill="none" stroke="#999" stroke-width="1.4"/><line x1="6.3" y1="6.3" x2="9" y2="9" stroke="#999" stroke-width="1.6"/></svg>
  </div>
</header>

<nav class="abs nav">
  <a class="active" style="width:62px">HOME</a>
  <a style="width:138px">TUTORIAL PACKAGES</a>
  <a style="width:181px">WEEKLY TIPS AND COMMENTS</a>
  <a style="width:77px">READING</a>
  <a style="width:85px">SPEAKING</a>
  <a style="width:84px">LISTENING</a>
  <a style="width:77px;border-right:0">WRITING</a>
</nav>

<section>
  <div class="abs hero" role="img" aria-label="Photo of a wooden pier stretching towards a cloudy sky"></div>
  <h1 class="abs hero-title">Typinon habent claritatem</h1>
  <p class="abs hero-sub">Duis autem vel eum iriure dolor</p>
  <p class="abs hero-text">Ut wisi enim ad minim veniam, quis nostrud exerci tation ullamcor<br>per suscipit lobortis nisl ut aliquip ex ea commodo consequat.</p>
  <div class="abs enroll">ENROLL NOW</div>
  <div class="abs dots"><i></i><i></i><i></i><i></i></div>

  <div class="abs video">
    <div class="abs video-frame" role="img" aria-label="Video still of a tutor in an office"></div>
    <svg class="abs" style="left:112px;top:50px" width="62" height="62" viewBox="0 0 62 62"><circle cx="31" cy="31" r="30" fill="rgba(40,40,40,.6)"/><path d="M24 19 L44 31 L24 43 Z" fill="#ddd"/></svg>
    <svg class="abs controls" width="284" height="24" viewBox="0 0 284 24">
      <path d="M8 8 L13 12 L8 16 Z" fill="#fff"/>
      <rect x="18" y="11" width="136" height="3" fill="#555"/>
      <rect x="18" y="11" width="86" height="3" fill="#d21d1d"/>
      <text x="158" y="15" font-size="7" fill="#fff" font-family="Open Sans,sans-serif">1:26 / <tspan fill="#999">3:22</tspan></text>
      <path d="M199 10 L202 10 L205 7.5 L205 16.5 L202 14 L199 14 Z" fill="#fff"/>
      <rect x="209" y="11" width="20" height="3" fill="#d21d1d"/>
      <rect x="236" y="5" width="1" height="14" fill="#444"/>
      <rect x="243" y="9" width="9" height="6" fill="none" stroke="#fff" stroke-width="1"/>
      <text x="258" y="15" font-size="7.5" font-weight="700" font-style="italic" fill="#fff" font-family="Open Sans,sans-serif">HD</text>
    </svg>
  </div>
</section>

<section>
  <h2 class="abs h-section welcome-h">WELCOME TO OUR WEBSITE</h2>
  <p class="abs welcome-p">Ut wisi enim ad minim veniam, quis nostrud exerci tation ullamcorper suscipit nisl ut aliquip ex ea commodo conseq<br>uat. Duis autem vel eum iriure dolor in it in vulputate velit esse molestie consequat, vel illum dolore eu feugiat nuafa<br>vero eros et accumsan et iusto odio dignissim qui blandit praesent luptatumzenit augue duis dolore te feugiat nulla f<br>acilisi. Nam liber tempor cum solutanofend option congue nihl imperdiet doming id quiod mazim placerat facer.</p>
  <ul class="abs features">
    <li>Lessons in reading, writing, listening and speaking</li>
    <li>Professional teacher feedback and tips.</li>
    <li>Voxly and practice with native speakers.</li>
    <li>Friendly and Approachable teachers.</li>
  </ul>

  <div class="abs cal">
    <div class="cal-head">
      <svg width="7" height="9" viewBox="0 0 7 9"><path d="M5 1 L1.5 4.5 L5 8" stroke="#fff" stroke-width="1.6" fill="none"/></svg>
      <span>January 2014</span>
      <svg width="7" height="9" viewBox="0 0 7 9"><path d="M2 1 L5.5 4.5 L2 8" stroke="#fff" stroke-width="1.6" fill="none"/></svg>
    </div>
    <div class="cal-grid">
      <span class="dn">MON</span><span class="dn">TUE</span><span class="dn">WED</span><span class="dn">THU</span><span class="dn">FRI</span><span class="dn">SAT</span><span class="dn">SUN</span>
      <span class="off ev">30</span><span>1</span><span class="ev">2</span><span>3</span><span>4</span><span>5</span><span>6</span>
      <span>7</span><span>8</span><span>9</span><span>10</span><span>11</span><span class="today ev">12</span><span>13</span>
      <span>14</span><span>15</span><span class="ev">16</span><span class="ev">17</span><span>18</span><span>19</span><span>20</span>
      <span class="ev">21</span><span>22</span><span>23</span><span>24</span><span>25</span><span>26</span><span>27</span>
      <span>28</span><span>29</span><span>30</span><span>31</span><span class="off">1</span><span class="off">2</span><span class="off">3</span>
    </div>
  </div>
</section>

<svg width="0" height="0" style="position:absolute">
  <symbol id="tick" viewBox="0 0 12 10"><path d="M1 5 L4.5 8.5 L11 1.5" stroke="#3aa64a" stroke-width="2.6" fill="none"/></symbol>
  <symbol id="cross" viewBox="0 0 10 10"><path d="M1.5 1.5 L8.5 8.5 M8.5 1.5 L1.5 8.5" stroke="#e4553c" stroke-width="2.6"/></symbol>
</svg>

<section>
  <h2 class="abs h-section pk-h">DIFFERENT PACKAGES OF ONLINE TUITION</h2>
  <div class="abs pk-frame"></div>

  <div class="abs card" style="left:64px;top:761px;width:243px;height:302px">
    <h3 style="margin-top:21px">Standard</h3>
    <p class="price">$19/month</p>
    <ul class="list">
      <li><svg width="12" height="10"><use href="#tick"/></svg>Download-Accelerators</li>
      <li><svg width="12" height="10"><use href="#tick"/></svg>Downloads resume</li>
      <li><svg width="12" height="10"><use href="#cross"/></svg>No downloads delay</li>
      <li><svg width="12" height="10"><use href="#cross"/></svg>No downloads captcha</li>
      <li><svg width="12" height="10"><use href="#cross"/></svg>No Advertisements</li>
    </ul>
    <div class="pay">Checkout with paywick</div>
  </div>

  <div class="abs card" style="left:519px;top:761px;width:242px;height:302px">
    <h3 style="margin-top:21px">Premium</h3>
    <p class="price">$39/month</p>
    <ul class="list">
      <li><svg width="12" height="10"><use href="#tick"/></svg>Download-Accelerators</li>
      <li><svg width="12" height="10"><use href="#tick"/></svg>Downloads resume</li>
      <li><svg width="12" height="10"><use href="#tick"/></svg>No downloads delay</li>
      <li><svg width="12" height="10"><use href="#cross"/></svg>No downloads captcha</li>
      <li><svg width="12" height="10"><use href="#cross"/></svg>No Advertisements</li>
    </ul>
    <div class="pay">Checkout with paywick</div>
  </div>

  <div class="abs card pop" style="left:309px;top:752px;width:210px;height:320px">
    <h3 style="margin-top:28px">Professional</h3>
    <p class="price">$59/month</p>
    <ul class="list">
      <li><svg width="12" height="10"><use href="#tick"/></svg>Download-Accelerators</li>
      <li><svg width="12" height="10"><use href="#tick"/></svg>Downloads resume</li>
      <li><svg width="12" height="10"><use href="#tick"/></svg>No downloads delay</li>
      <li><svg width="12" height="10"><use href="#tick"/></svg>No downloads captcha</li>
      <li><svg width="12" height="10"><use href="#cross"/></svg>No Advertisements</li>
    </ul>
    <div class="pay">Checkout with paywick</div>
  </div>
  <div class="abs ribbon"><b>POPULAR</b></div>
</section>

<footer class="abs footer">
  <p class="abs footer-links">Home | Tutorial Packages | Weekly Tips and Comments | Reading | Speaking | Listening | Writing</p>
  <p class="abs copyright">Copyright © 2013. All Rights Reserved.</p>
  <div class="abs social">
    <span style="background:#3b5cb0">friendbook</span>
    <span style="background:#1fa0e0">chirpnet</span>
    <span style="background:#f07a1a">RSS</span>
    <span style="background:#d8262a">vidtube</span>
  </div>
</footer>

</body>
</html>
```